Flat Belly Design Graphics for Social

I want to create 9 social media graphics (new Instagram size 4:5 (1080 x 1350 pixels) focusing on our Flat Belly Graphics, using the pics attached. Use the attached pics, NO RANDOM STOCK PHOTOGRAPHY. For the color scheme of the graphics, the color palette is attached. YOU MUST POST ALL 9 GRAPHICS IN ONE ENTRY.
Using the 3 titles below, create one set of graphics. 1) with all text, then for the others, use the pictures as detailed below in IMPORTANT:
1. Ten-Week Bright Morning Reboot
2. The Quick Garden Kitchen Menu Guide
3. Studio Habits for Lasting Energy Past Midlife - Zero Gym Needed
IMPORTANT:
Only use RK Pic 1 and RK Pic 2 with the title, Ten-Week Bright Morning Reboot
Only use meal plan1 and meal plan2 pics with the title, Quick Garden Kitchen Menu Guide
Only use studio habits 1 and studio habits 2 pics with the title, Studio Habits for Lasting Energy Past Midlife - Zero Gym Needed
women over 40

```html
<!DOCTYPE html>
<html lang="en">
<head>
<meta charset="utf-8">
<title>Morning Reboot Social Set</title>
<link rel="stylesheet" href="https://fonts.googleapis.com/css2?family=Poppins:wght@700&family=Playfair+Display:wght@900&family=Yeseva+One&family=Yellowtail&display=swap">
<style>
:root{
  --forest:#324d49;
  --rose:#e59bb0;
  --rose-pale:#f6d7df;
  --mauve:#c47d93;
  --ribbon:#e9a2b5;
  --sky:#5ec3dc;
  --white:#ffffff;
  --ink:#111111;
  --canvas:#ffffff;
}
*{margin:0;padding:0;box-sizing:border-box}
html,body{width:1200px;height:371px;overflow:hidden;background:var(--canvas)}
.set{position:relative;width:1200px;height:371px}
.post{position:absolute;top:7px;width:285px;height:357px;overflow:hidden;box-shadow:0 1px 4px rgba(0,0,0,.18)}
.post svg.layer{position:absolute;inset:0}
.txt{position:absolute;white-space:nowrap}

/* Post 1: menu guide */
.menu{left:9px;background:var(--forest)}
.menu .frame{position:absolute;left:6px;top:6px;right:6px;bottom:6px;border:1px solid rgba(255,255,255,.85)}
.menu .kicker{left:0;right:0;top:33px;text-align:center;font:700 20px/1 'Poppins',sans-serif;color:var(--white)}
.menu .script{left:0;right:0;top:72px;text-align:center;font:400 24px/1 'Yellowtail',cursive;color:var(--white)}

/* Post 2: all-text studio habits */
.habits{left:311px;background:linear-gradient(180deg,var(--rose) 0%,var(--rose-pale) 100%)}
.habits .frame{position:absolute;left:5px;top:5px;right:5px;bottom:5px;border:1.5px solid var(--white)}
.habits .serif{font:900 30px/1 'Playfair Display',serif;color:var(--ink);left:28px}
.habits .on-band{color:var(--white)}
.habits .sub{font:900 21px/1 'Playfair Display',serif;color:var(--ink);left:28px}

/* Post 3: morning reboot */
.reboot{left:611px;background:linear-gradient(180deg,#6f5245 0%,#b9a596 45%,#e9e2dc 100%)}
.reboot .kicker{left:0;right:0;top:288px;text-align:center;font:700 19px/1 'Poppins',sans-serif;color:var(--white)}
.reboot .script{left:0;right:0;top:314px;text-align:center;font:400 23px/1 'Yellowtail',cursive;color:var(--white)}

/* Post 4: studio habits with photo */
.studio{left:906px;background:var(--sky)}
.studio .headline{left:0;right:0;top:14px;text-align:center;font:400 21px/1 'Yeseva One',serif;color:var(--white)}
.studio .ribbon-text{left:0;right:0;top:52px;text-align:center;font:400 21px/1 'Yeseva One',serif;color:var(--forest)}
.studio .script{left:0;right:0;top:90px;text-align:center;font:400 15px/1 'Yellowtail',cursive;color:var(--white)}
</style>
</head>
<body>
<main class="set">

  <section class="post menu">
    <svg class="layer" width="285" height="357" viewBox="0 0 285 357">
      <defs>
        <linearGradient id="mealTones" x1="0" y1="0" x2="1" y2="1">
          <stop offset="0" stop-color="#c99a86"/>
          <stop offset=".5" stop-color="#6b4a35"/>
          <stop offset="1" stop-color="#8d9b57"/>
        </linearGradient>
      </defs>
      <rect x="16" y="19" width="28" height="3" rx="1.5" fill="#fff" opacity=".85"/>
      <circle cx="253" cy="139" r="16" fill="#dfe6e4" opacity=".85" role="img" aria-label="Round patterned accent"/>
      <path d="M150 110 q-12 2 -4 8 q10 6 4 14 l-3 -4 m3 4 l3 -4" fill="none" stroke="#fff" stroke-width="1.6" stroke-linecap="round"/>
      <path d="M0 210 Q142 130 285 205 L285 357 L0 357 Z" fill="#fff"/>
      <path d="M0 216 Q142 138 285 211 L285 357 L0 357 Z" fill="url(#mealTones)" role="img" aria-label="Overhead table of healthy meal ingredients with a printed meal plan sheet"/>
    </svg>
    <div class="frame"></div>
    <p class="txt kicker">The Quick Garden</p>
    <p class="txt script">Kitchen Menu Guide</p>
  </section>

  <section class="post habits">
    <div class="frame"></div>
    <svg class="layer" width="285" height="357" viewBox="0 0 285 357">
      <circle cx="12" cy="13" r="9" fill="none" stroke="#fff" stroke-width="4"/>
      <circle cx="240" cy="36" r="22" fill="#fff" opacity=".75" role="img" aria-label="Round patterned accent"/>
      <path d="M5 96 H187 L205 114 L187 132 H5 Z" fill="var(--forest)"/>
      <path d="M5 192 H200 L217 209.5 L200 227 H5 Z" fill="var(--forest)"/>
      <rect x="15" y="338" width="60" height="6" fill="var(--ink)" opacity=".8" role="img" aria-label="Wave line accent"/>
      <circle cx="273" cy="344" r="8" fill="none" stroke="var(--ink)" stroke-width="3.5"/>
    </svg>
    <p class="txt serif" style="top:53px">Studio</p>
    <p class="txt serif on-band" style="top:99px">Habits</p>
    <p class="txt serif" style="top:146px;font-size:26px">for Lasting Energy</p>
    <p class="txt serif on-band" style="top:195px;font-size:28px">Past Midlife</p>
    <p class="txt sub" style="top:248px">Zero Gym Needed</p>
  </section>

  <section class="post reboot">
    <svg class="layer" width="285" height="357" viewBox="0 0 285 357">
      <rect x="0" y="0" width="285" height="357" fill="transparent" role="img" aria-label="Smiling woman in a cropped white sweater pointing at her waist in a kitchen"/>
      <path d="M0 226 Q142 318 285 226 L285 357 L0 357 Z" fill="var(--mauve)" opacity=".92"/>
    </svg>
    <p class="txt kicker">Ten-Week</p>
    <p class="txt script">Bright Morning Reboot</p>
  </section>

  <section class="post studio">
    <svg class="layer" width="285" height="357" viewBox="0 0 285 357">
      <defs>
        <linearGradient id="friendsTones" x1="0" y1="0" x2="0" y2="1">
          <stop offset="0" stop-color="#5ec3dc"/>
          <stop offset=".3" stop-color="#b98a72"/>
          <stop offset=".75" stop-color="#d9b3a8"/>
          <stop offset="1" stop-color="#5a7fa8"/>
        </linearGradient>
      </defs>
      <path d="M34 48 H252 L244 62.5 L252 77 H34 L42 62.5 Z" fill="var(--ribbon)"/>
      <path d="M258 62 q22 20 4 42 q-6 6 -16 9 l5 -5 m-5 5 l6 3" fill="none" stroke="#fff" stroke-width="1.6" stroke-linecap="round"/>
      <path d="M56 357 L60 160 Q100 120 150 130 Q200 120 240 150 L245 357 Z" fill="url(#friendsTones)" role="img" aria-label="Two women sharing a surprised whisper against a blue backdrop"/>
      <circle cx="10" cy="133" r="20" fill="#fff" opacity=".7" role="img" aria-label="Round patterned accent"/>
      <rect x="250" y="337" width="28" height="5" fill="#fff" opacity=".85" role="img" aria-label="Wave line accent"/>
    </svg>
    <p class="txt headline">Studio Habits for Lasting</p>
    <p class="txt ribbon-text">Energy Past Midlife</p>
    <p class="txt script">Zero Gym Needed</p>
  </section>

</main>
</body>
</html>
```